Premium Relish Company Needs Postcard size Shelf talker

Business name: Corbin & Jules Velvet Foods
www.corbinandjules.com.au
Product/service/brand name:
Corbin & Jules Velvet Foods. We produce the MOST delicious premium relishes in Australia and they retail in all premium deli’s, butchers, and high end supermarkets in NSW and VIC. Please see our website for further details: www.corbinandjules.com.au
Key Objective:
Design a Post card size shelf talker. These are small signs that attach to a retail shelf ledge. Shelf Talkers are an effective way to attract and communicate with customer's in-store as they are wandering the aisles. OUR key objective is to attract EVERY single potential customer to the relish and make them buy.
Marketing objectives:
Build Brand awareness, Increase sales by creating enough curiosity for a customer to purchase the product immediately without trying it. We want something that will catch the eye and increase their interest until picking up the product off the shelf and putting it in their basket seems the most logical and sensible option to them, as opposed to them feeling they are involved in a great risk.
Our Image:
We like humour and our two phrases "Relish just got saucy" & "Makes everything better. - EVERYTHING!" reflect this. We like to appeal to their happier side when they purchase our product.
We don't want busy imagery.
Please avoid the brash colours and imagery associated with take away food. This is premium cuisine, with a modern urban angle – but not up itself. It is the perfect accompaniment to a fantastic quality BBQ for average Australian and the perfect condiment to always keep in the fridge as it is the only condiment on the market that is FULL of REAL flavour.
Key Concepts:
FUNNY, URBAN, RELEVANT
FUNNY – Chaotic Adult fun. A strong sense of the child within.
NOT CHILDLIKE
URBAN – Stay away from the conservative “country image” that most of our competitors use. We don’t want to look like we were made out on a farm somewhere.
RELEVANT – THIS IS SOMETHING EVERYONE WILL WANT TO EAT!
It is relevant to everyone and will make everything they eat it with better. Everything.
Target Audience:
Our target audience is ANYONE who loves premium quality food and is willing to pay a little bit more for a great tasting product as opposed to settling for a cheaper relish that is below average, processed and filled with additives and nasties. Our current demographic is middle-class, comfortable income, mainly Anglo-Saxon Australians - age range is quite broad from young up to professionals to comfortably set retirees.
Non Negotiable Elements of the design: The Logo
Size: Postcard - PORTRAIT ORIENTATION
File format: Happy for you to suggest which format is best.
Stock : 350gsm paper
Colours: Dominant colour must be a “Roma Tomato” Red, however keep colours down to Maximum 4
Design:
Double sided .
Front will have writing as follows with long logo incorporated as well:
CORBIN & JULES (LOGO)
Relish just got saucy (this should fit right under the logo )
• 100% Natural
• Luscious Full Flavour
• Award Winning
• Gluten Free
• Vegan Friendly
• Modern Australian Taste
.........with echoes of tradition.
Makes everything better. Everything!
Back will have burger image with short logo above it
Updates
SORRY! Forgot to mention that design layout needs to be PORTRAIT. Thanks
Reason: I have been away and need a bit more time to consider designs.

```html
<!DOCTYPE html>
<html lang="en">
<head>
<meta charset="utf-8">
<title>Corbin &amp; Jules Velvet Foods – Shelf Talker</title>
<link rel="stylesheet" href="https://fonts.googleapis.com/css2?family=Cardo:wght@400;700&family=Special+Elite&display=swap">
<style>
  :root {
    --roma-red: #8a1e1e;
    --ink-black: #000000;
    --paper-white: #ffffff;
    --sheet-bg: #ffffff;
    --label-ink: #222222;
    --gold-light: #f6c35a;
    --gold-dark: #b8731c;
    --burger-warm: #c9862f;
    --burger-deep: #5a2a1a;
    --leaf-green: #5e8f2a;
  }
  * { box-sizing: border-box; margin: 0; padding: 0; }
  html, body { width: 1200px; height: 885px; overflow: hidden; background: var(--sheet-bg); }
  .sheet { position: relative; width: 1200px; height: 885px; }

  .side-label {
    position: absolute; top: 29px;
    font-family: Arial, Helvetica, sans-serif; font-size: 19px; color: var(--label-ink);
  }
  .side-label--front { left: 12px; }
  .side-label--back { left: 607px; }

  /* ---------- Front ---------- */
  .card-front {
    position: absolute; left: 10px; top: 53px; width: 584px; height: 755px;
    background: var(--ink-black); overflow: hidden; border: 1px solid #444;
  }
  .front-header { position: absolute; left: 0; top: 0; width: 584px; height: 200px; }
  .brand-name {
    position: absolute; left: 0; top: 30px; width: 584px; text-align: center;
    font-family: "Special Elite", cursive; font-size: 62px; line-height: 70px; font-weight: 400;
    color: var(--paper-white); letter-spacing: 1px; white-space: nowrap;
  }
  .tagline {
    position: absolute; left: 0; top: 122px; width: 584px; text-align: center;
    font-family: "Cardo", serif; font-weight: 700; font-size: 29px; line-height: 34px;
    color: var(--ink-black); white-space: nowrap;
  }
  .benefits {
    position: absolute; left: 30px; top: 206px; list-style: none;
    font-family: "Cardo", serif; font-weight: 700; font-size: 24px; color: var(--paper-white);
    line-height: 34.6px;
  }
  .benefits li::before { content: "•"; display: inline-block; width: 25px; }
  .promise-seal {
    position: absolute; left: 368px; top: 208px; width: 180px; height: 180px; border-radius: 50%;
    background: var(--roma-red); border: 5px solid var(--paper-white);
    display: flex; align-items: center; justify-content: center;
  }
  .promise-seal p {
    font-family: "Special Elite", monospace; font-size: 19px; line-height: 22px;
    color: var(--paper-white); text-align: center; transform: rotate(20deg);
  }
  .award-seal {
    position: absolute; left: 42px; top: 437px; width: 210px; height: 210px; border-radius: 50%;
    background: radial-gradient(circle at 40% 35%, var(--gold-light), var(--gold-dark) 75%);
    border: 6px solid #e0a040;
  }
  .tradition-line {
    position: absolute; left: 251px; top: 474px; width: 300px; text-align: center;
    font-family: "Cardo", serif; font-weight: 700; font-size: 40px; line-height: 58px;
    color: var(--paper-white); white-space: nowrap;
  }
  .footer-band {
    position: absolute; left: 0; top: 657px; width: 584px; height: 75px;
    border-top: 6px solid var(--paper-white); border-bottom: 6px solid var(--paper-white);
    background: var(--roma-red); background-clip: padding-box;
  }
  .footer-band::before {
    content: ""; position: absolute; left: 0; right: 0; top: 0; bottom: 0;
    border-top: 4px solid var(--ink-black); border-bottom: 4px solid var(--ink-black);
  }
  .web-address {
    position: absolute; left: 0; top: 8px; width: 584px; text-align: center;
    font-family: "Cardo", serif; font-weight: 700; font-size: 35px; color: var(--paper-white);
    white-space: nowrap;
  }

  /* ---------- Back ---------- */
  .card-back {
    position: absolute; left: 606px; top: 53px; width: 582px; height: 755px; overflow: hidden;
    border: 1px solid #444;
  }
  .burger-photo {
    position: absolute; inset: 0;
    background:
      radial-gradient(ellipse at 60% 10%, #e9c47c 0%, transparent 30%),
      radial-gradient(ellipse at 50% 65%, #f0a520 0%, transparent 35%),
      linear-gradient(180deg, #d9a760 0%, #7a9a3a 28%, #6b3a4a 45%, var(--burger-warm) 62%, var(--burger-deep) 75%, var(--leaf-green) 85%, #d8b070 100%);
  }
  .back-brand {
    position: absolute; left: 205px; top: 578px; width: 360px; text-align: left;
    font-family: "Special Elite", cursive; font-size: 64px; line-height: 66px;
    color: var(--paper-white); white-space: nowrap;
  }
</style>
</head>
<body>
<div class="sheet">
  <span class="side-label side-label--front">Front</span>
  <span class="side-label side-label--back">Back</span>

  <section class="card-front">
    <svg class="front-header" width="584" height="200" viewBox="0 0 584 200" aria-hidden="true">
      <path d="M0 0 H584 V118 Q292 240 0 118 Z" fill="var(--roma-red)"/>
      <path d="M0 118 Q292 240 584 118" fill="none" stroke="var(--paper-white)" stroke-width="5"/>
    </svg>
    <h1 class="brand-name">Corbin &amp; Jules</h1>
    <p class="tagline">Relish Just Got Saucy</p>

    <ul class="benefits">
      <li>100% Natural</li>
      <li>Luscious Full Flavour</li>
      <li>Award Winning</li>
      <li>Gluten Free</li>
      <li>Vegan Friendly</li>
      <li>Modern Australian Taste</li>
    </ul>

    <div class="promise-seal"><p>Makes<br>everything<br>better.<br>Everything</p></div>

    <div class="award-seal" aria-hidden="true"></div>
    <p class="tradition-line">....with echoes<br>of tradition.</p>

    <div class="footer-band"><p class="web-address">www.corbinandjules.com.au</p></div>
  </section>

  <section class="card-back">
    <div class="burger-photo" role="img" aria-label="Close-up photo of a gourmet burger with melted cheese, red onion, pickles and relish"></div>
    <p class="back-brand">Corbin<br>&amp; Jules</p>
  </section>
</div>
</body>
</html>
```